I will ask the design of the business card

We are looking for business card design of the new company "R DOVE PAYGRID WORKS LLC." Based in Azerbaijan.
In case
We are working on Azerbaijan to set up the first exchange of crypto currencies.

The key currency used in exchanges is called "PLUME".
In case
We are doing project to make crypto currency infrastructure.

We provide state-of-the-art technology to the world.

```html
<!DOCTYPE html>
<html lang="en">
<head>
<meta charset="UTF-8">
<title>R Dove PayGrid Works LLC. – Business Card</title>
<link href="https://fonts.googleapis.com/css2?family=Montserrat:wght@300;400;500;700&display=swap" rel="stylesheet">
<style>
  :root {
    --backdrop: #cfd3d5;
    --paper: #f6f6f4;
    --ink: #1b1b1d;
    --ink-soft: #4a4a4c;
    --brand-blue: #1670c4;
    --brand-blue-dark: #0f58a8;
    --edge-blue: #1048b0;
    --white: #ffffff;
  }
  * { margin: 0; padding: 0; box-sizing: border-box; }
  html, body { width: 1200px; height: 1061px; overflow: hidden; }
  body {
    background: var(--backdrop);
    font-family: "Montserrat", sans-serif;
    display: flex;
    flex-direction: column;
    align-items: center;
    justify-content: center;
    gap: 70px;
  }
  .card {
    position: relative;
    width: 700px;
    height: 400px;
    overflow: hidden;
    box-shadow: 0 14px 30px rgba(0,0,0,0.18);
  }

  /* ---------- Front card ---------- */
  .card-front { background: var(--ink); border-bottom: 5px solid var(--edge-blue); }
  .front-brand {
    position: absolute; left: 0; top: 0; bottom: 0; width: 290px;
    background: var(--paper);
    display: flex; flex-direction: column; align-items: center; justify-content: center;
    gap: 18px; text-align: center;
  }
  .brand-dot { width: 70px; height: 70px; border-radius: 50%; background: var(--brand-blue); }
  .brand-name {
    font-weight: 500; font-size: 21px; letter-spacing: 1px; line-height: 1.35;
    color: var(--ink-soft);
  }
  .name-ribbon {
    position: absolute; left: 262px; right: 0; top: 112px; height: 84px;
    background: linear-gradient(90deg, var(--brand-blue-dark), var(--brand-blue));
    display: flex; align-items: center; gap: 26px; padding-left: 40px;
  }
  .ribbon-tab {
    position: absolute; left: 262px; top: 96px; width: 28px; height: 16px;
    background: var(--brand-blue-dark);
    clip-path: polygon(100% 0, 100% 100%, 0 100%);
  }
  .icon-box {
    width: 40px; height: 40px; border-radius: 8px;
    background: var(--brand-blue);
    display: flex; align-items: center; justify-content: center; flex-shrink: 0;
  }
  .name-ribbon .icon-box { background: var(--brand-blue-dark); }
  .holder-name { color: var(--white); font-weight: 700; font-size: 27px; letter-spacing: 1px; }
  .holder-title { color: var(--white); font-weight: 400; font-size: 16px; letter-spacing: 1px; margin-top: 2px; }
  .contact-list {
    position: absolute; left: 302px; top: 226px;
    display: flex; gap: 34px;
  }
  .contact-icons { display: flex; flex-direction: column; gap: 14px; }
  .contact-lines {
    color: var(--white); font-size: 20px; font-weight: 400; line-height: 32px;
    letter-spacing: 0.5px; padding-top: 4px;
  }

  /* ---------- Back card ---------- */
  .card-back { background: var(--paper); border-bottom: 5px solid var(--edge-blue); }
  .back-brand {
    position: absolute; left: 0; right: 0; top: 62px;
    display: flex; flex-direction: column; align-items: center; gap: 18px;
  }
  .back-brand .brand-dot { width: 76px; height: 76px; }
  .currency-name { font-weight: 300; font-size: 58px; letter-spacing: 4px; color: var(--brand-blue); }
  .address-band {
    position: absolute; left: 0; right: 0; bottom: 0; height: 130px;
    background: var(--ink); border-top: 9px solid var(--edge-blue);
    display: flex; align-items: center; justify-content: center;
  }
  .pin-tab {
    position: absolute; left: 50%; top: -26px; transform: translateX(-50%);
    width: 58px; height: 40px; background: var(--brand-blue);
    clip-path: polygon(14% 0, 86% 0, 100% 70%, 50% 100%, 0 70%);
    display: flex; align-items: center; justify-content: center; padding-bottom: 6px;
  }
  .address-lines {
    color: var(--white); font-size: 18px; line-height: 28px; text-align: center;
    letter-spacing: 0.5px; margin-top: 18px;
  }
</style>
</head>
<body>

  <section class="card card-back" aria-label="Business card back">
    <div class="back-brand">
      <span class="brand-dot"></span>
      <span class="currency-name">PLUME</span>
    </div>
    <div class="address-band">
      <div class="pin-tab">
        <svg width="16" height="20" viewBox="0 0 16 20"><path d="M8 0a7 7 0 0 0-7 7c0 5 7 13 7 13s7-8 7-13a7 7 0 0 0-7-7z" fill="#fff"/><circle cx="8" cy="7" r="2.6" fill="#1670c4"/></svg>
      </div>
      <p class="address-lines">AZ1010, 27 Nizami Ave.<br>Baku City, Azerbaijan</p>
    </div>
  </section>

  <section class="card card-front" aria-label="Business card front">
    <div class="front-brand">
      <span class="brand-dot"></span>
      <span class="brand-name">R DOVE PAYGRID<br>WORKS LLC.</span>
    </div>
    <div class="ribbon-tab"></div>
    <div class="name-ribbon">
      <span class="icon-box">
        <svg width="20" height="22" viewBox="0 0 20 22"><circle cx="10" cy="6" r="5" fill="#fff"/><path d="M0 22c0-6 4.5-9 10-9s10 3 10 9z" fill="#fff"/></svg>
      </span>
      <div>
        <p class="holder-name">ELNUR KARIMOV</p>
        <p class="holder-title">CEO DIRECTOR</p>
      </div>
    </div>
    <div class="contact-list">
      <div class="contact-icons">
        <span class="icon-box">
          <svg width="20" height="20" viewBox="0 0 24 24"><path d="M6.6 10.8a15 15 0 0 0 6.6 6.6l2.2-2.2a1 1 0 0 1 1-.25 11.4 11.4 0 0 0 3.6.57 1 1 0 0 1 1 1V20a1 1 0 0 1-1 1A17 17 0 0 1 3 4a1 1 0 0 1 1-1h3.5a1 1 0 0 1 1 1c0 1.25.2 2.45.57 3.6a1 1 0 0 1-.25 1z" fill="#fff"/></svg>
        </span>
        <span class="icon-box">
          <svg width="20" height="20" viewBox="0 0 24 24" fill="none" stroke="#fff" stroke-width="2"><circle cx="12" cy="12" r="9"/><path d="M3 12h18M12 3c3 3 3 15 0 18M12 3c-3 3-3 15 0 18"/></svg>
        </span>
      </div>
      <p class="contact-lines">+994 12 480 2719<br>+994 12 480 2720<br>hello@dovepaygrid.az<br>dovepaygrid.az</p>
    </div>
  </section>

</body>
</html>
```